Law Offices business card

Hi there, I'll need business card for the Law Offices of Colin Matheny. The information must convey his strategic approach and quick resolution to complex business litigation needs. Please emphasize Civil Litigation, Corporate Law, Business Governance and Real Estate Law. Colin has over 25 years of experience in these fields.The card should be modern and edgy and the message should be clear. Please consult his current website for ideas.

```html
<!DOCTYPE html>
<html lang="en">
<head>
<meta charset="utf-8">
<title>Colin Matheny – Attorney</title>
<link rel="stylesheet" href="https://fonts.googleapis.com/css2?family=Carlito:wght@400;700&display=swap">
<style>
  :root {
    --page: #ffffff;
    --card: #e2e2e2;
    --card-light: #e9e9e9;
    --frame: #a3a3a3;
    --ink: #0f3d0f;
  }
  * { margin: 0; padding: 0; box-sizing: border-box; }
  html, body {
    width: 1200px;
    height: 850px;
    overflow: hidden;
    background: var(--page);
  }
  .canvas {
    position: relative;
    width: 1200px;
    height: 850px;
  }
  .card {
    position: absolute;
    left: 117px;
    top: 61px;
    width: 917px;
    height: 635px;
    border: 7px solid var(--frame);
    background: radial-gradient(ellipse at 40% 40%, var(--card-light), var(--card));
    font-family: "Carlito", "Calibri", sans-serif;
    color: var(--ink);
  }
  .card > * {
    position: absolute;
    text-align: right;
    white-space: nowrap;
    font-weight: 700;
  }
  .name {
    top: 21px;
    right: 67px;
    font-size: 73px;
    line-height: 1;
  }
  .title-rule {
    top: 114px;
    right: 249px;
    width: 308px;
    height: 3px;
    background: var(--ink);
  }
  .title {
    top: 89px;
    right: 71px;
    font-size: 45px;
    line-height: 1;
  }
  .firm {
    top: 167px;
    right: 61px;
    font-size: 40px;
    line-height: 1;
  }
  .address {
    top: 223px;
    right: 65px;
    font-size: 33px;
    line-height: 39px;
    font-style: normal;
  }
  .profile {
    top: 318px;
    right: 57px;
    font-size: 32px;
    line-height: 39.2px;
  }
</style>
</head>
<body>
  <div class="canvas">
    <section class="card">
      <h1 class="name">Colin Matheny</h1>
      <div class="title-rule"></div>
      <p class="title">Attorney</p>
      <h2 class="firm">Law Offices of Colin Matheny, P. A.</h2>
      <address class="address">
        118B Harbor Lane<br>
        Coral Point, Florida 33921
      </address>
      <p class="profile">
        Colin Matheny's strategic approach to<br>
        Civil Litigation, Corporate Law,<br>
        Business Governance and Real Estate law<br>
        over 25 years has earned him a reputation<br>
        for quick resolution.
      </p>
    </section>
  </div>
</body>
</html>
```